Business card update

Opening a subsidiary of my company in the USA and need to update my logo.
Updates

Reason: Give more time to a good design.

I made a mistake on my briefing. It's only the business card. Thanks for alerting me on the mistake.

All the best

Teodoro

Target Market(s)

We are an Executive Search company and our target audience are executives in large corporations.

Industry/Entity Type

Business

Requirements
Must have
• Keep the logo. In the US the company is called Delia Brunet Executive Search.

```html
<!DOCTYPE html>
<html lang="en">
<head>
<meta charset="utf-8">
<title>Delia Brunet Executive Search – Business Card</title>
<link rel="stylesheet" href="https://fonts.googleapis.com/css2?family=Arvo:wght@700&family=Open+Sans:wght@400;600&display=swap">
<style>
  :root {
    --page-bg: #ebebeb;
    --card-top: #ffffff;
    --card-bottom: #ececec;
    --teal: #2fa3b1;
    --ink: #3e4657;
    --body-text: #4a4f59;
    --rule: #c7cdd3;
  }
  * { box-sizing: border-box; margin: 0; padding: 0; }
  html, body { width: 1200px; height: 900px; overflow: hidden; }
  body {
    background: var(--page-bg);
    display: flex;
    align-items: center;
    justify-content: center;
    font-family: "Open Sans", Arial, sans-serif;
  }
  .business-card {
    position: relative;
    width: 980px;
    height: 560px;
    background: linear-gradient(180deg, var(--card-top) 0%, var(--card-top) 45%, var(--card-bottom) 100%);
    box-shadow: 0 10px 28px rgba(0,0,0,0.18);
    overflow: hidden;
  }
  .edge-band {
    position: absolute;
    top: 0; right: 0;
    width: 22px; height: 100%;
    background: var(--teal);
  }
  .brand {
    position: absolute;
    top: 70px; left: 58px;
    display: flex;
    align-items: center;
    gap: 14px;
    padding-bottom: 12px;
    border-bottom: 1px solid var(--rule);
  }
  .brand-dot {
    width: 26px; height: 26px;
    border-radius: 50%;
    background: var(--teal);
  }
  .brand-name {
    font-family: "Open Sans", Arial, sans-serif;
    font-weight: 400;
    font-size: 26px;
    letter-spacing: 4px;
    text-transform: uppercase;
    color: var(--ink);
  }
  .holder {
    position: absolute;
    top: 250px; left: 96px;
  }
  .holder-name {
    font-family: "Arvo", Georgia, serif;
    font-weight: 700;
    font-size: 32px;
    color: var(--ink);
  }
  .holder-role {
    margin-top: 8px;
    font-size: 24px;
    color: var(--teal);
  }
  .address {
    position: absolute;
    top: 352px; left: 96px;
    font-size: 21px;
    line-height: 1.35;
    color: var(--body-text);
    font-style: normal;
  }
  .contact-list {
    position: absolute;
    top: 432px; left: 118px;
    list-style: none;
    font-size: 21px;
    line-height: 1.3;
    color: var(--body-text);
  }
  .contact-list li {
    display: flex;
    align-items: center;
    gap: 10px;
  }
  .contact-icon { width: 18px; height: 18px; flex: none; }
</style>
</head>
<body>
  <article class="business-card">
    <div class="edge-band"></div>

    <header class="brand">
      <span class="brand-dot"></span>
      <span class="brand-name">Delia Brunet</span>
    </header>

    <section class="holder">
      <h1 class="holder-name">Teodoro S. Brunet</h1>
      <p class="holder-role">CEO / Founder</p>
    </section>

    <address class="address">
      4820 Harbor View Ave Suite 310<br>
      Coral Point FL 33190
    </address>

    <ul class="contact-list">
      <li>
        <svg class="contact-icon" viewBox="0 0 20 20" aria-hidden="true">
          <path fill="#2fa3b1" d="M2 6c0-2 1.5-3 8-3s8 1 8 3v2h-4V6.5H6V8H2z"/>
          <rect x="4" y="9" width="12" height="8" rx="1.5" fill="#2fa3b1"/>
          <circle cx="10" cy="13" r="2" fill="#ffffff"/>
        </svg>
        305 555 0147
      </li>
      <li>
        <svg class="contact-icon" viewBox="0 0 20 20" aria-hidden="true">
          <rect x="1.5" y="4" width="17" height="12" rx="1" fill="none" stroke="#2fa3b1" stroke-width="2"/>
          <path d="M2 5l8 6 8-6" fill="none" stroke="#2fa3b1" stroke-width="2"/>
        </svg>
        tbrunet@dbexecutivesearch.com
      </li>
      <li>
        <svg class="contact-icon" viewBox="0 0 20 20" aria-hidden="true">
          <circle cx="10" cy="10" r="8" fill="none" stroke="#2fa3b1" stroke-width="2"/>
          <ellipse cx="10" cy="10" rx="3.5" ry="8" fill="none" stroke="#2fa3b1" stroke-width="1.6"/>
          <path d="M2 10h16" stroke="#2fa3b1" stroke-width="1.6"/>
        </svg>
        www.dbexecutivesearch.com
      </li>
    </ul>
  </article>
</body>
</html>
```